Construction material supplies company business card ****

1. Full company name “K T Masonry Works Ltd”
I am after a Business card design for the company as a whole. We are better known in Solomon Islands as “K T Masonry” for short.

We are a building materials supplier of
Ready Mixed Concrete, Bricks and Blocks,
Quarry products- gravel, aggregates, sand etc.
Cement distributor/retailer of reputable brands.
Other prefab concrete products. Culverts, wave breakers, concrete retaining blocks etc.

2. Competitive Advantage over Competition: Quality, efficient, professional, dependable, reliable

3. We want people to feel trust worthy, high quality, strong when they see our brand

5. No preference to color. Maybe more sturdy and corporate. Not fancy.

Industry/Entity Type

CONSTRUCTION SUPPLY

Contact Information for Business Card

Name, Position, office phone mob phone, email

Requirements
Must have
• the company logo
Nice to have
• would like to see a mixture of designs, of with logo only and also with simple graphic designs to bring out the company whilst still have the strong sturdy professional feeling

```html
<!DOCTYPE html>
<html lang="en">
<head>
<meta charset="utf-8">
<title>K T Masonry — Business Card</title>
<link href="https://fonts.googleapis.com/css2?family=Montserrat:ital,wght@0,400;0,600;0,700;1,400&display=swap" rel="stylesheet">
<style>
  :root {
    --navy: #143f63;
    --navy-deep: #0f3352;
    --navy-bright: #1d5f97;
    --white: #ffffff;
    --muted: #5a6470;
    --stage: #e9ecef;
  }
  * { box-sizing: border-box; margin: 0; padding: 0; }
  html, body { width: 1200px; height: 900px; overflow: hidden; }
  body {
    background: var(--stage);
    font-family: "Montserrat", Arial, sans-serif;
    display: flex; flex-direction: column; align-items: center; justify-content: center;
    gap: 48px;
  }
  .card {
    width: 640px; height: 366px; border-radius: 22px; overflow: hidden; position: relative;
    box-shadow: 0 10px 28px rgba(0,0,0,.18);
  }

  /* Front */
  .card--front { background: var(--white); }
  .front__brand {
    position: absolute; left: 54px; top: 48px;
    display: flex; align-items: center; gap: 14px;
    color: var(--navy); font-weight: 700; font-size: 34px; letter-spacing: 1px; text-transform: uppercase;
  }
  .brand__square { width: 34px; height: 34px; background: currentColor; }
  .front__band {
    position: absolute; left: 0; right: 0; top: 196px; height: 128px; background: var(--navy);
  }
  .front__band::before {
    content: ""; position: absolute; left: 64px; top: -12px;
    border-left: 12px solid transparent; border-right: 12px solid transparent; border-bottom: 12px solid var(--navy);
  }
  .front__person { position: absolute; left: 112px; top: 128px; color: var(--navy); }
  .person__name { font-weight: 700; font-size: 22px; letter-spacing: 1px; text-transform: uppercase; }
  .person__role { font-style: italic; font-size: 14px; color: var(--muted); margin-top: 2px; }
  .front__contacts {
    position: absolute; left: 54px; top: 214px; list-style: none;
    color: var(--white); font-size: 15px; line-height: 28px;
  }
  .front__contacts li { display: flex; align-items: center; gap: 10px; }
  .front__contacts svg { width: 14px; height: 14px; fill: none; stroke: var(--white); stroke-width: 1.6; }
  .front__mark {
    position: absolute; right: 88px; top: 168px; width: 120px; height: 120px; background: var(--white);
  }

  /* Back */
  .card--back { background: var(--navy); }
  .back__pattern {
    position: absolute; inset: 0;
    background: linear-gradient(135deg, var(--navy-deep) 0%, var(--navy) 55%, var(--navy-bright) 100%);
  }
  .back__brand {
    position: absolute; left: 50%; top: 50%; transform: translate(-50%, -50%);
    display: flex; align-items: center; gap: 16px;
    color: var(--white); font-weight: 700; font-size: 40px; letter-spacing: 1.5px; text-transform: uppercase;
    white-space: nowrap;
  }
  .back__brand .brand__square { width: 40px; height: 40px; }
</style>
</head>
<body>
  <section class="card card--front">
    <div class="front__band"></div>
    <div class="front__brand"><span class="brand__square"></span>K T Masonry</div>
    <div class="front__person">
      <p class="person__name">Daniel Rourke</p>
      <p class="person__role">President</p>
    </div>
    <ul class="front__contacts">
      <li><svg viewBox="0 0 16 16"><path d="M4 1.5l2.5 3-1.5 1.5a9 9 0 0 0 5 5l1.5-1.5 3 2.5-1.5 2.5C7 14 2 9 1.5 3z"/></svg>985-210-4476</li>
      <li><svg viewBox="0 0 16 16"><rect x="1.5" y="3.5" width="13" height="9"/><path d="M1.5 3.5l6.5 5 6.5-5"/></svg>info@KTMasonry.com</li>
      <li><svg viewBox="0 0 16 16"><circle cx="8" cy="8" r="6.5"/><path d="M1.5 8h13M8 1.5c3 3.5 3 9.5 0 13M8 1.5c-3 3.5-3 9.5 0 13"/></svg>www.KTMasonry.com</li>
    </ul>
    <div class="front__mark"></div>
  </section>

  <section class="card card--back">
    <div class="back__pattern" role="img" aria-label="Repeating embossed brand-mark pattern in deep blue tones"></div>
    <div class="back__brand"><span class="brand__square"></span>K T Masonry</div>
  </section>
</body>
</html>
```